AGP letterhead

We need a letterhead design for our new company based in Los Angeles called "Amber Gate Pictures". We develop film and television projects. We work with investors, financiers, film production companies, film distribution and sales companies as well as studios. We would like to incorporate our logo (see attached) but make the letterhead simple and elegant. We need to include: logo, company address, phone number and company website.
Updates

Hello designers, Thanks for your submissions. For our letterhead, we are looking for something more simple and elegant. No heavy bars or lines. Make it feel light and clean. Not a lot of ink on the page. Use the logo and contact info but think "clean", "streamlined" and mostly white paper. Looking forward to seeing more... thanks! Amber Gate Pictures team

Target Market(s)

Studio executives, talent agents and agencies, financiers, investors.

Industry/Entity Type

It Company

Requirements
Must have
• Amber Gate Pictures logo (see attached). Logo may be cropped and altered appropriately for elegant letterhead design.
• Please include:
• COMPANY ADDRESS:
• Tolvane Arts Park
• 2850 Delmore Street
• Crest Hall, 2nd Floor
• Manhattan Beach, CA 90266
• COMPANY WEBSITE:
• www.ambergatepicturesco.example
• COMPANY PHONE NUMBER:
• 555-604-2187

```html
<!DOCTYPE html>
<html lang="en">
<head>
<meta charset="utf-8">
<title>Amber Gate Pictures – Letterhead</title>
<link rel="stylesheet" href="https://fonts.googleapis.com/css2?family=Montserrat:wght@400;500;700&display=swap">
<style>
  :root {
    --backdrop: #e9eaec;
    --paper: #ffffff;
    --ink: #2b3a42;
    --ink-soft: #4a565c;
    --brand: #1b8ec4;
    --rule: #9aa3a8;
  }
  * { box-sizing: border-box; margin: 0; padding: 0; }
  html, body {
    width: 1200px; height: 936px; overflow: hidden;
    background: var(--backdrop);
    font-family: "Montserrat", sans-serif;
    color: var(--ink);
  }
  .letterhead {
    position: absolute; left: 296px; top: 38px;
    width: 608px; height: 860px;
    background: var(--paper);
    box-shadow: 0 2px 10px rgba(0,0,0,0.08);
  }
  .masthead {
    position: absolute; left: 44px; top: 44px;
    display: flex; align-items: center;
  }
  .brand {
    display: flex; flex-direction: column; align-items: center;
    width: 110px;
  }
  .brand-dot {
    width: 30px; height: 30px; border-radius: 50%;
    background: var(--brand); margin-bottom: 6px;
  }
  .brand-name {
    font-size: 8.5px; font-weight: 700; letter-spacing: 1.4px;
    color: var(--brand); text-align: center; line-height: 1.25;
    text-transform: uppercase;
  }
  .brand-tagline {
    margin-top: 3px;
    font-size: 4.5px; font-weight: 500; letter-spacing: 0.8px;
    color: var(--ink-soft); text-transform: uppercase;
  }
  .masthead-divider {
    width: 1px; height: 72px; background: var(--rule);
    margin: 0 14px 0 10px;
  }
  .contact-list { list-style: none; font-size: 8.5px; line-height: 1.45; }
  .contact-list li { display: flex; align-items: flex-start; }
  .contact-icon { width: 9px; height: 9px; margin: 2px 6px 0 0; flex: none; fill: var(--ink); }
  .contact-indent { padding-left: 15px; }

  .edge-rule {
    position: absolute; right: 24px; top: 400px;
    width: 6px; height: 400px; background: var(--ink);
  }
  .edge-web {
    position: absolute; right: 34px; top: 400px;
    writing-mode: vertical-rl;
    font-size: 8px; letter-spacing: 0.6px; color: var(--ink-soft);
  }
  .corner-mark {
    position: absolute; right: 8px; bottom: 14px;
    width: 44px; height: 44px;
  }
</style>
</head>
<body>
  <main class="letterhead">
    <header class="masthead">
      <div class="brand">
        <span class="brand-dot"></span>
        <span class="brand-name">Amber Gate Pictures</span>
        <span class="brand-tagline">Film &amp; Television Development</span>
      </div>
      <span class="masthead-divider"></span>
      <ul class="contact-list">
        <li><svg class="contact-icon" viewBox="0 0 10 10"><path d="M5 0a3.4 3.4 0 0 0-3.4 3.4C1.6 6 5 10 5 10s3.4-4 3.4-6.6A3.4 3.4 0 0 0 5 0zm0 4.8a1.4 1.4 0 1 1 0-2.8 1.4 1.4 0 0 1 0 2.8z"/></svg>2850 Delmore Street, Crest Hall, 2nd Floor</li>
        <li class="contact-indent">Tolvane Arts Park, Manhattan Beach, CA 90266</li>
        <li><svg class="contact-icon" viewBox="0 0 10 10"><path d="M2.2 0.5l1.6 2.2-1 1.1a6 6 0 0 0 3.4 3.4l1.1-1 2.2 1.6-.9 1.7C4.6 9.5.5 5.4 0.5 1.4z"/></svg>555-604-2187</li>
        <li><svg class="contact-icon" viewBox="0 0 10 10"><path d="M0 2h10v6H0zm.8.6L5 5.5l4.2-2.9V2.6H.8z"/></svg>nora@ambergatepicturesco.example</li>
        <li><svg class="contact-icon" viewBox="0 0 10 10"><circle cx="5" cy="5" r="4.4" fill="none" stroke="#2b3a42" stroke-width="1"/><path d="M.6 5h8.8M5 .6c-2.4 2.6-2.4 6.2 0 8.8M5 .6c2.4 2.6 2.4 6.2 0 8.8" fill="none" stroke="#2b3a42" stroke-width="0.7"/></svg>ambergatepicturesco.example</li>
      </ul>
    </header>

    <div class="edge-rule"></div>
    <span class="edge-web">www.ambergatepicturesco.example</span>
    <svg class="corner-mark" viewBox="0 0 44 44" role="img" aria-label="Brand ornament area">
      <circle cx="22" cy="22" r="20" fill="none" stroke="#2b3a42" stroke-width="2"/>
    </svg>
  </main>
</body>
</html>
```